Ad-Services Website

The project is for an agency which provides a 360 service around the world of printing and advertising. Without much focus on the advertising per say, but much more focus on the medium on which advertisement can be achieved, such as banners, moving banners, boards and so on.

Futhermore more the company deals with material printing so it has advertising agencies as clients.

Finally it represents several companies in Greece for materials around advertising such as stands, ad-walls, banners and so on.

The webpage needs to have web 2.0 look an feel, and it will lack in content, therefore the focus should not be in large sections of text.

I can have a pdf sent with a small presentation that was done to the client, and the structure to which he agreed to

The following website has the look & feel of what we are looking for

http://www.lumtaro.gr

The companies current website where you can get the colors and logos from is

http://korvibelt.gr
Updates

Hello,

Thank you all very much for your designs, we really appreciate your contribution.

Maybe in our next project we can work together.

Best Regards,
Manos

Industry/Entity Type

Advertising

```html
<!DOCTYPE html>
<html lang="en">
<head>
<meta charset="utf-8">
<title>Nexora Advertising</title>
<link rel="stylesheet" href="https://fonts.googleapis.com/css2?family=Source+Sans+3:wght@400;600;700&display=swap">
<style>
  :root {
    --ink: #1d1d1d;
    --muted: #444;
    --brand: #1a5472;
    --nav-top: #2f87a9;
    --nav-bottom: #0c4b66;
    --rule: #d5d5d5;
    --rule-soft: #e4e4e4;
    --frame: #dcdcdc;
    --paper: #ffffff;
  }
  * { box-sizing: border-box; margin: 0; padding: 0; }
  html, body { width: 1200px; height: 849px; overflow: hidden; background: var(--paper); }
  body { position: relative; font-family: "Source Sans 3", "Myriad Pro", sans-serif; color: var(--ink); }
  .abs { position: absolute; }

  .brand-name { left: 162px; top: 12px; color: var(--brand); font-weight: 700; line-height: 1; }
  .brand-name .word { display: block; font-size: 40px; letter-spacing: -1px; }
  .brand-name .sub { display: block; font-size: 18px; text-align: right; margin-top: -2px; }

  .main-nav { left: 570px; top: 36px; display: flex; gap: 3px; }
  .main-nav a {
    width: 91px; height: 26px; border-radius: 3px;
    background: linear-gradient(var(--nav-top), var(--nav-bottom));
    color: #fff; text-decoration: none; font-size: 12px; text-transform: uppercase;
    display: flex; align-items: center; justify-content: center;
  }
  .main-nav a:last-child { width: 92px; }

  .easel-frame { left: 178px; top: 93px; width: 340px; height: 155px; border: 7px solid var(--frame); border-radius: 4px; background: #fff; padding: 2px; }
  .easel-photo { width: 100%; height: 100%; background: linear-gradient(#b9cfe0 0%, #e0d7a8 35%, #6f8a4a 70%, #47672f 100%); }
  .easel-stand-area { left: 275px; top: 248px; width: 146px; height: 57px; background: linear-gradient(#d9b48a, #efe2d2); }

  .hero { left: 559px; top: 93px; width: 478px; height: 255px; background: linear-gradient(#c9d3d6 0%, #d8dcd8 30%, #5d7f43 45%, #44702c 75%, #2f5620 100%); box-shadow: 0 10px 12px -6px rgba(0,0,0,.45); }

  .welcome { left: 163px; top: 328px; width: 376px; }
  .welcome h1 { font-size: 21px; font-weight: 400; color: var(--brand); padding-bottom: 3px; border-bottom: 3px solid var(--rule-soft); }
  .welcome p { margin-top: 8px; font-size: 11.2px; line-height: 18.5px; color: var(--muted); text-align: justify; }

  .gallery { left: 561px; top: 380px; width: 477px; height: 76px; }
  .gallery .arrow { position: absolute; top: 24px; }
  .gallery .arrow.prev { left: 7px; }
  .gallery .arrow.next { left: 463px; }
  .gallery .divider { position: absolute; top: 0; width: 1px; height: 76px; background: var(--rule-soft); }
  .thumb { position: absolute; top: 9px; width: 70px; height: 55px; border: 3px solid #d9d9d9; border-radius: 3px; box-shadow: 0 2px 3px rgba(0,0,0,.3); }
  .thumb.t1 { left: 32px; background: linear-gradient(#9cc6df, #e9eef1); }
  .thumb.t2 { left: 141px; background: linear-gradient(90deg, #cfd1c8, #7d8a78, #cfd1c8); }
  .thumb.t3 { left: 252px; background: linear-gradient(#2f5a9a, #8fb1d9); }
  .thumb.t4 { left: 363px; background: linear-gradient(#dcd6cf, #b4a89a); }
  .gallery-rule { left: 561px; top: 473px; width: 477px; height: 1px; background: var(--rule); }

  .services-area { left: 157px; top: 480px; width: 120px; height: 122px; border-radius: 50%; background: radial-gradient(circle, #e9e7e8 0%, #f4f3f3 100%); }
  .doc-badge { left: 310px; top: 514px; width: 28px; height: 36px; background: #c4271d; border-radius: 2px; }
  .partner { left: 372px; top: 522px; display: flex; align-items: center; gap: 5px; font-size: 17px; font-weight: 700; color: var(--ink); }
  .partner .dot { width: 12px; height: 12px; border-radius: 50%; background: #f0c419; }
  .vrule { left: 506px; top: 486px; width: 1px; height: 119px; background: var(--rule); }

  .contact { right: 163px; top: 496px; text-align: right; font-size: 11.5px; color: var(--muted); font-style: normal; line-height: 16px; }
  .contact .company { font-size: 13.5px; font-weight: 700; color: var(--ink); }
  .contact .address { margin-top: 13px; }
  .contact .phone { margin-top: 21px; }
  .contact .phone b { color: var(--ink); }
  .contact .email { margin-top: 3px; }

  .site-footer { left: 165px; top: 623px; width: 876px; height: 216px; border: 1px solid var(--rule); }
  .footer-col { position: absolute; top: 22px; font-size: 11.5px; line-height: 16px; }
  .footer-col h2 { font-size: 11.5px; font-weight: 700; margin-bottom: 12px; }
  .footer-col li { list-style: none; margin-bottom: 12.5px; }
  .footer-divider { position: absolute; top: 28px; width: 1px; height: 117px; background: var(--rule); }
  .footer-rule { position: absolute; left: 31px; top: 160px; width: 796px; height: 1px; background: var(--rule); }
  .follow { position: absolute; left: 632px; top: 178px; display: flex; align-items: center; font-size: 11.5px; }
  .follow span { margin-right: 17px; }
  .follow i { display: block; width: 22px; height: 22px; border-radius: 3px; margin-right: 8px; }
</style>
</head>
<body>
  <div class="abs brand-name"><span class="word">nexora</span><span class="sub">advertising</span></div>

  <nav class="abs main-nav">
    <a href="#">About us</a><a href="#">Advertising</a><a href="#">Displays</a><a href="#">Printing</a><a href="#">Brands</a>
  </nav>

  <div class="abs easel-frame"><div class="easel-photo" role="img" aria-label="Photo of three branded pop-up tents on a lawn"></div></div>
  <div class="abs easel-stand-area" role="img" aria-label="Wooden easel holding the framed photo"></div>

  <div class="abs hero" role="img" aria-label="Photo of an outdoor billboard in a green field"></div>

  <section class="abs welcome">
    <h1>Welcome to our site</h1>
    <p>Lorem Ipsum is simply dummy text of the printing and typesetting industry. Lorem Ipsum has been the industry's standard dummy text ever since the 1500s, when an unknown printer took a galley of type and scrambled it to make a type specimen book. It has survived not only five centuries, but also the leap into electronic typesetting, remaining essentially unchanged.</p>
  </section>

  <div class="abs gallery">
    <svg class="arrow prev" width="10" height="16" viewBox="0 0 10 16"><path d="M8 1 2 8l6 7" fill="none" stroke="#222" stroke-width="2.5"/></svg>
    <div class="thumb t1" role="img" aria-label="Billboard thumbnail"></div>
    <div class="divider" style="left:120px"></div>
    <div class="thumb t2" role="img" aria-label="Street advert thumbnail"></div>
    <div class="divider" style="left:232px"></div>
    <div class="thumb t3" role="img" aria-label="Poster advert thumbnail"></div>
    <div class="divider" style="left:343px"></div>
    <div class="thumb t4" role="img" aria-label="Outdoor display thumbnail"></div>
    <svg class="arrow next" width="10" height="16" viewBox="0 0 10 16"><path d="M2 1l6 7-6 7" fill="none" stroke="#222" stroke-width="2.5"/></svg>
  </div>
  <div class="abs gallery-rule"></div>

  <div class="abs services-area" role="img" aria-label="Illustration linking advertising, print and display services"></div>
  <div class="abs doc-badge"></div>
  <div class="abs partner"><span class="dot"></span>Tendara</div>
  <div class="abs vrule"></div>

  <address class="abs contact">
    <div class="company">Nexora Advertising &amp; Printing LTD</div>
    <div class="address">Pelekanou 12, Neo Psychiko, 15451</div>
    <div class="phone">t.<b>+30 2104417382</b></div>
    <div class="email">info@nexoraprint.gr</div>
  </address>

  <footer class="abs site-footer">
    <div class="footer-col" style="left:29px"><h2>About Us</h2><ul><li>Clients</li></ul></div>
    <div class="footer-divider" style="left:111px"></div>
    <div class="footer-col" style="left:137px"><h2>Advertising</h2><ul><li>Services Implementations</li><li>Services Implementations</li></ul></div>
    <div class="footer-divider" style="left:314px"></div>
    <div class="footer-col" style="left:348px;top:20px"><h2>Displays</h2><ul><li>Services Implementations</li><li>Services Implementations</li></ul></div>
    <div class="footer-divider" style="left:523px"></div>
    <div class="footer-col" style="left:554px"><h2>Printing</h2><ul><li>Services Implementations</li><li>Services Implementations</li></ul></div>
    <div class="footer-divider" style="left:720px"></div>
    <div class="footer-col" style="left:762px"><h2>Brands</h2><ul><li>Velo Displays</li><li>Standrix</li><li>Signelo</li><li>Tendara</li></ul></div>
    <div class="footer-rule"></div>
    <div class="follow"><span>Follow Us on</span><i style="background:#3b5a98"></i><i style="background:#3fb5e6"></i><i style="background:#1b75b0"></i><i style="background:#f08a24"></i></div>
  </footer>
</body>
</html>
```